WordPress Design for both website and landing page for an expert

I need a clean and stylish design for my new website. I work as an expert (see attached file WHY HOW WHAT), my product is expert opinion (reports) for company evaluations You can use all of the attached pictures colored or black / white. The person is me, you can add other pictures, if you want. The design should be clean and stylish, so you could use white, black, gray, silver and / or one additional color. I have added an idea about my website, see attached file CONCEPT WEBSITE If you have any more information, please do not hesitate to contact us 'Hesitate to ask me ...

```html
<!DOCTYPE html>
<html lang="en">
<head>
<meta charset="utf-8">
<title>Lukas Verhoeven – Expert for company valuations</title>
<link href="https://fonts.googleapis.com/css2?family=Montserrat:wght@300;400;500;600&family=Merriweather:wght@300;400&display=swap" rel="stylesheet">
<style>
:root{
  --stage:#aab1b6;
  --ink:#000000;
  --panel:#0a0a0a;
  --white:#ffffff;
  --muted:#9a9a9a;
  --soft:#cfcfcf;
  --line:#2c2c2c;
  --field:#1c1c1c;
  --photo-dark:#3c3c3c;
  --photo-mid:#777a7c;
  --photo-light:#c9ccce;
  --accent-blue:#5a7fa8;
}
*{box-sizing:border-box;margin:0;padding:0}
html,body{width:1073px;height:1200px;overflow:hidden}
body{background:var(--stage);font-family:'Montserrat',sans-serif;color:var(--white);position:relative}
.screen{position:absolute;background:var(--panel);overflow:hidden;box-shadow:0 8px 24px rgba(0,0,0,.18)}
.brand{position:absolute;font-family:'Montserrat',sans-serif;font-weight:500;font-size:9px;letter-spacing:2px;color:var(--white)}
.nav-label{position:absolute;font-size:6px;font-weight:500;letter-spacing:1.6px;color:var(--white);text-transform:uppercase}
.close{position:absolute;width:10px;height:10px}
.photo{position:absolute}
.display{font-weight:300;letter-spacing:5px;text-transform:uppercase;color:var(--white)}
.tagline{font-weight:400;color:var(--white)}
.copy{font-family:'Merriweather',serif;font-weight:300;color:var(--soft);line-height:1.7}

/* hero */
.hero{left:32px;top:32px;width:560px;height:330px;background:var(--photo-dark)}
.hero .photo{inset:0;background:linear-gradient(100deg,#4a4a4a 0%,#6d6f70 35%,#5a5b5c 55%,#3d3d3d 100%)}
.hero .brand{left:22px;top:22px}
.hero .title{position:absolute;left:0;right:0;top:140px;text-align:center}
.hero .title .display{font-size:30px}
.hero .title .tagline{font-size:11px;margin-top:6px}
.hero .top{left:0;right:0;top:26px;text-align:center}
.hero .bottom{left:0;right:0;bottom:22px;text-align:center}
.hero .left{left:14px;top:165px;transform:rotate(-90deg);transform-origin:left top}
.hero .right{right:14px;top:140px;transform:rotate(90deg);transform-origin:right top}

/* mobile */
.mobile{left:612px;top:62px;width:130px;height:264px;border-radius:16px;background:var(--photo-light)}
.mobile .photo{inset:0;background:linear-gradient(180deg,#d7d3cc 0%,#b9b6b0 45%,#5e6062 75%,#2e2f31 100%)}

/* laptop */
.laptop{left:762px;top:102px;width:279px;height:182px}
.laptop .brand{left:12px;top:12px;font-size:7px}
.laptop .nav-label{left:0;right:0;top:15px;text-align:center;font-size:4.5px}
.laptop .close{right:12px;top:12px;width:7px;height:7px}
.laptop .photo{left:30px;top:46px;width:110px;height:88px;background:linear-gradient(135deg,#e9e9e9 0%,#c7c9cb 55%,#8fa4bc 100%)}
.laptop .headline{position:absolute;left:62px;top:78px;font-size:13px;letter-spacing:3px;line-height:1.35}
.laptop .copy{position:absolute;left:65px;top:148px;width:160px;font-size:3.6px;line-height:1.6}

/* pages */
.page{top:392px;width:323px;height:776px}
.page .brand{left:18px;top:20px}
.page .head{left:0;right:0;top:24px;text-align:center}
.page .close{right:18px;top:20px}
.why{left:32px}
.about{left:375px}
.contact{left:718px}

/* why page */
.why .photo{left:34px;top:72px;width:176px;height:130px;background:linear-gradient(135deg,#eeeeee 0%,#cfd1d3 55%,#8aa2bd 100%)}
.why .headline{position:absolute;left:84px;top:118px;font-size:17px;letter-spacing:4px;line-height:1.4}
.why .intro{position:absolute;left:60px;top:228px;width:210px;font-size:6px}
.section-title{position:absolute;font-weight:600;font-size:10px;color:var(--white)}
.why .section-title{left:60px;top:296px}
.why .method{position:absolute;left:60px;top:316px;width:210px;font-size:6px}
.why .steps{position:absolute;left:60px;top:368px;width:210px;display:flex;gap:24px}
.step{flex:1}
.step .bubble{width:40px;height:40px;border-radius:50%;background:var(--line);display:flex;align-items:center;justify-content:center}
.step .copy{font-size:5.5px;margin-top:12px}

/* about page */
.about .photo{left:34px;top:72px;width:255px;height:150px;background:linear-gradient(90deg,#b9bcbe 0%,#8e9194 30%,#3a3b3d 50%,#9fa2a5 70%,#dcdedf 100%)}
.about .title{position:absolute;left:34px;width:255px;top:124px;text-align:center}
.about .title .display{font-size:20px;letter-spacing:4px}
.about .title .tagline{font-size:8px;margin-top:4px}
.about .intro{position:absolute;left:60px;top:244px;width:205px;font-size:5.6px}
.about .reasons{position:absolute;left:0;right:0;top:298px;text-align:center;font-weight:600;font-size:10px;line-height:1.5}
.timeline{position:absolute;left:157px;top:348px;width:1px;height:120px;background:var(--line)}
.about .marker{position:absolute;left:143px;top:366px;width:29px;height:29px;border-radius:50%;background:var(--panel);border:1px solid #444;display:flex;align-items:center;justify-content:center}
.about .reason-label{position:absolute;left:185px;top:364px;font-size:6px;font-weight:600;letter-spacing:1.4px}
.about .reason-copy{position:absolute;left:185px;top:376px;width:100px;font-size:5.5px}

/* contact page */
.contact .photo{left:34px;top:72px;width:255px;height:150px;background:linear-gradient(90deg,#5f7ea3 0%,#35506e 18%,#2a2b2d 24%,#232426 100%)}
.contact .headline{position:absolute;left:0;right:0;top:130px;text-align:center;font-size:18px;letter-spacing:4px;line-height:1.3}
.contact .details{position:absolute;left:34px;width:255px;top:240px;display:flex;justify-content:center;gap:44px;text-align:center}
.detail svg{display:block;margin:0 auto 5px}
.detail .copy{font-family:'Montserrat',sans-serif;font-size:4.8px;line-height:1.5;color:var(--soft)}
.detail .email{font-size:6px;color:var(--white)}
.contact .section-title{left:0;right:0;top:300px;text-align:center;line-height:1.4}
.form{position:absolute;left:40px;top:340px;width:243px}
.form .row{display:flex;gap:8px}
.field{flex:1;height:13px;background:var(--field);font-size:4.5px;letter-spacing:1px;color:var(--muted);padding:4px 6px}
.area{height:70px;margin-top:10px;background:var(--field)}
.send{margin:14px auto 0;width:70px;height:18px;border:1px solid #555;font-size:5.5px;letter-spacing:1.5px;text-align:center;line-height:16px}
</style>
</head>
<body>

<section class="screen hero" aria-label="Home">
  <div class="photo" role="img" aria-label="Black and white portrait of the expert"></div>
  <span class="brand">L. VERHOEVEN</span>
  <span class="nav-label top">What I do</span>
  <span class="nav-label left">About</span>
  <span class="nav-label right">Contact</span>
  <div class="title">
    <h1 class="display">Lukas Verhoeven</h1>
    <p class="tagline">Expert for company valuations</p>
  </div>
  <span class="nav-label bottom">Why / How I do</span>
</section>

<section class="screen mobile" aria-label="Mobile home">
  <div class="photo" role="img" aria-label="Full-length photo of the expert in a dark suit"></div>
</section>

<section class="screen laptop" aria-label="Why I do">
  <span class="brand">L. VERHOEVEN</span>
  <span class="nav-label">Why / How I do</span>
  <svg class="close" viewBox="0 0 10 10"><path d="M1 1L9 9M9 1L1 9" stroke="#fff" stroke-width="1.2"/></svg>
  <div class="photo" role="img" aria-label="Hands working on a financial chart report"></div>
  <h2 class="headline display">Economy is my<br>passion</h2>
  <p class="copy">Economy is made in numbers. Sometimes it is difficult to find the right numbers. I am always interested in finding out how economy works and which numbers tell the really true story.</p>
</section>

<section class="screen page why" aria-label="Why and how I do">
  <span class="brand">L. VERHOEVEN</span>
  <span class="nav-label head">Why / How I do</span>
  <svg class="close" viewBox="0 0 10 10"><path d="M1 1L9 9M9 1L1 9" stroke="#fff" stroke-width="1.2"/></svg>
  <div class="photo" role="img" aria-label="Hands working on a financial chart report"></div>
  <h2 class="headline display">Economy is my<br>passion</h2>
  <p class="copy intro">Economy is made in numbers. Sometimes it is difficult to find the right numbers. I am always interested in finding out, how economy works and which numbers tell the really true story. I want to know it.</p>
  <h3 class="section-title">How I do?</h3>
  <p class="copy method">Each report begins with understanding. So I ask you questions and listen very carefully.</p>
  <div class="steps">
    <div class="step">
      <div class="bubble"><svg width="18" height="18" viewBox="0 0 18 18" fill="none" stroke="#fff" stroke-width="1.2"><rect x="3" y="2" width="12" height="14"/><path d="M6 6h6M6 9h6M6 12h4"/></svg></div>
      <p class="copy">In the preparation of each report I follow one defined process, step by step.</p>
    </div>
    <div class="step">
      <div class="bubble"><svg width="18" height="18" viewBox="0 0 18 18" fill="none" stroke="#fff" stroke-width="1.2"><rect x="2" y="3" width="14" height="12"/><path d="M5 12V9M9 12V6M13 12V8"/></svg></div>
      <p class="copy">This approach keeps each special valuation clear and well founded.</p>
    </div>
  </div>
</section>

<section class="screen page about" aria-label="About">
  <span class="brand">L. VERHOEVEN</span>
  <span class="nav-label head">About</span>
  <svg class="close" viewBox="0 0 10 10"><path d="M1 1L9 9M9 1L1 9" stroke="#fff" stroke-width="1.2"/></svg>
  <div class="photo" role="img" aria-label="Photo of the expert in a bright office hallway"></div>
  <div class="title">
    <h2 class="display">Lukas Verhoeven</h2>
    <p class="tagline">Expert for company valuations</p>
  </div>
  <p class="copy intro">Sed ut perspiciatis unde omnis iste natus voluptatem accusantium doloremque laudantium, totam rem aperiam, eaque ipsa quae inventore veritatis et quasi architecto beatae vitae dicta sunt explicabo.</p>
  <h3 class="reasons">3 reasons, Why you should<br>work with me.</h3>
  <div class="timeline"></div>
  <div class="marker"><svg width="11" height="11" viewBox="0 0 12 12" fill="none" stroke="#fff" stroke-width="1"><rect x="1.5" y="2.5" width="9" height="8"/><path d="M1.5 5h9M4 1v3M8 1v3"/></svg></div>
  <span class="reason-label">FAST PROCESS</span>
  <p class="copy reason-copy">You will receive your report promptly (within a maximum of 21 days after receipt of all required documents)</p>
</section>

<section class="screen page contact" aria-label="Contact">
  <span class="brand">L. VERHOEVEN</span>
  <span class="nav-label head">Contact</span>
  <svg class="close" viewBox="0 0 10 10"><path d="M1 1L9 9M9 1L1 9" stroke="#fff" stroke-width="1.2"/></svg>
  <div class="photo" role="img" aria-label="City skyline at dusk beside a dark street map"></div>
  <h2 class="headline display">Contact<br>me</h2>
  <div class="details">
    <div class="detail">
      <svg width="9" height="11" viewBox="0 0 10 12" fill="none" stroke="#fff" stroke-width="1"><path d="M5 11C2 7.5 1 5.8 1 4.2A4 4 0 0 1 9 4.2C9 5.8 8 7.5 5 11Z"/><circle cx="5" cy="4.3" r="1.3"/></svg>
      <p class="copy">12 Harbor Lane<br>Riverton 40117<br>Germany</p>
    </div>
    <div class="detail">
      <svg width="11" height="9" viewBox="0 0 12 9" fill="none" stroke="#fff" stroke-width="1"><rect x="0.5" y="0.5" width="11" height="8"/><path d="M0.5 0.5L6 5l5.5-4.5"/></svg>
      <p class="copy email">info@verhoeven-valuations.com</p>
      <p class="copy">Reply within a day</p>
    </div>
  </div>
  <h3 class="section-title">How can I help<br>you today?</h3>
  <div class="form">
    <div class="row">
      <div class="field">NAME</div>
      <div class="field">EMAIL</div>
      <div class="field">PHONE</div>
    </div>
    <div class="area"></div>
    <div class="send">SEND</div>
  </div>
</section>

</body>
</html>
```